Real Estate Business Card

On the front side I want to have my info, my brokerage info.
On the back side I want have my complany’s logo, website and Facebook link. I will provide all this once I select a design.

I would like to see Black background and gold text, Dark Blue and gold text and White and blue text designs

Font styles to use
Sans Serif
Script

```html
<!DOCTYPE html>
<html lang="en">
<head>
<meta charset="UTF-8">
<title>Northpeak Realty Business Card</title>
<link rel="stylesheet" href="https://fonts.googleapis.com/css2?family=Montserrat:wght@800&family=Work+Sans:wght@400;500&family=Great+Vibes&display=swap">
<style>
  :root {
    --backdrop: #1d1d1f;
    --card: #1f1f21;
    --card-edge: #2b2b2e;
    --gold: #c9a55a;
    --gold-soft: #dcc08a;
    --ink-soft: #d9d2c3;
    --badge: #f4f4f4;
  }
  * { box-sizing: border-box; margin: 0; padding: 0; }
  html, body { width: 1200px; height: 900px; overflow: hidden; }
  body {
    background: var(--backdrop);
    font-family: "Work Sans", Arial, sans-serif;
    color: var(--ink-soft);
    position: relative;
  }
  .card {
    position: absolute;
    left: 250px;
    width: 700px;
    height: 400px;
    background: linear-gradient(135deg, #232325 0%, var(--card) 60%, #1a1a1c 100%);
    border: 1px solid var(--card-edge);
  }
  .card--back { top: 30px; }
  .card--front { top: 470px; }

  /* Back side */
  .brand-mark {
    position: absolute;
    left: 0; right: 0; top: 140px;
    display: flex;
    align-items: center;
    justify-content: center;
    gap: 14px;
  }
  .brand-mark__square { width: 34px; height: 34px; background: var(--gold); }
  .brand-mark__name {
    font-family: "Montserrat", Arial, sans-serif;
    font-weight: 800;
    font-size: 46px;
    letter-spacing: 1px;
    color: var(--gold);
    text-transform: uppercase;
  }
  .back-links {
    position: absolute;
    left: 0; right: 0; top: 236px;
    display: flex;
    justify-content: center;
    gap: 36px;
    list-style: none;
    font-size: 18px;
    color: var(--gold-soft);
  }
  .back-links li { display: flex; align-items: center; gap: 8px; }
  .back-links svg { width: 14px; height: 14px; flex: none; }

  /* Front side */
  .front-logo {
    position: absolute;
    left: 40px; top: 160px;
    width: 270px;
    display: flex;
    align-items: center;
    gap: 12px;
  }
  .front-logo__square { width: 30px; height: 30px; background: var(--gold); flex: none; }
  .front-logo__name {
    font-family: "Montserrat", Arial, sans-serif;
    font-weight: 800;
    font-size: 32px;
    color: var(--gold);
    text-transform: uppercase;
    line-height: 1.1;
  }
  .divider {
    position: absolute;
    left: 330px; top: 60px;
    width: 2px; height: 190px;
    background: var(--gold);
  }
  .contact {
    position: absolute;
    left: 360px; top: 44px;
    width: 320px;
  }
  .contact__name {
    font-family: "Great Vibes", cursive;
    font-size: 44px;
    color: var(--gold);
    line-height: 1;
  }
  .contact__role { font-size: 17px; margin-top: 2px; color: var(--gold-soft); }
  .contact__address { font-size: 17px; margin-top: 12px; line-height: 1.35; }
  .contact__list { list-style: none; margin-top: 10px; }
  .contact__item {
    display: flex; align-items: center; gap: 10px;
    font-size: 17px; line-height: 1.4;
  }
  .contact__item svg { width: 12px; height: 12px; flex: none; }
  .contact__highlight { color: var(--gold); }
  .partner-badges {
    position: absolute;
    left: 360px; top: 310px;
    display: flex; gap: 12px;
  }
  .partner-badge { width: 130px; height: 46px; background: var(--badge); }
</style>
</head>
<body>
  <section class="card card--back" aria-label="Card back">
    <div class="brand-mark">
      <span class="brand-mark__square"></span>
      <span class="brand-mark__name">Northpeak Realty</span>
    </div>
    <ul class="back-links">
      <li>
        <svg viewBox="0 0 12 12" aria-hidden="true"><circle cx="6" cy="6" r="5" fill="none" stroke="#c9a55a" stroke-width="1.1"/><ellipse cx="6" cy="6" rx="2.2" ry="5" fill="none" stroke="#c9a55a" stroke-width="1"/><path d="M1 6 H11" stroke="#c9a55a" stroke-width="1"/></svg>
        www.northpeakrealty.com
      </li>
      <li>
        <svg viewBox="0 0 12 12" aria-hidden="true"><circle cx="6" cy="6" r="5" fill="none" stroke="#c9a55a" stroke-width="1.2"/></svg>
        /northpeakrealty
      </li>
    </ul>
  </section>

  <section class="card card--front" aria-label="Card front">
    <div class="front-logo">
      <span class="front-logo__square"></span>
      <span class="front-logo__name">Northpeak Realty</span>
    </div>
    <div class="divider"></div>
    <div class="contact">
      <p class="contact__name">Daniel Reyes</p>
      <p class="contact__role">Director</p>
      <p class="contact__address">1580 Cedar Ave #310<br>Brookfield, Alberta T5K 4R1</p>
      <ul class="contact__list">
        <li class="contact__item">
          <svg viewBox="0 0 12 12" aria-hidden="true"><path d="M3 1 L5 3.5 L4 5 Q5 7 7 8 L8.5 7 L11 9 L9.5 11 Q4 10.5 1 3 Z" fill="none" stroke="#c9a55a" stroke-width="1.2"/></svg>
          +1 555-214-7730
        </li>
        <li class="contact__item">
          <svg viewBox="0 0 12 12" aria-hidden="true"><rect x="1" y="2.5" width="10" height="7" fill="none" stroke="#c9a55a" stroke-width="1.2"/><path d="M1 2.5 L6 6.5 L11 2.5" fill="none" stroke="#c9a55a" stroke-width="1.2"/></svg>
          hello@northpeakrealty.com
        </li>
        <li class="contact__item">
          <svg viewBox="0 0 12 12" aria-hidden="true"><circle cx="6" cy="6" r="5" fill="none" stroke="#c9a55a" stroke-width="1.1"/><ellipse cx="6" cy="6" rx="2.2" ry="5" fill="none" stroke="#c9a55a" stroke-width="1"/><path d="M1 6 H11" stroke="#c9a55a" stroke-width="1"/></svg>
          <span>www.<span class="contact__highlight">northpeakrealty</span>.com</span>
        </li>
      </ul>
    </div>
    <div class="partner-badges">
      <div class="partner-badge" role="img" aria-label="Brokerage partner badge"></div>
      <div class="partner-badge" role="img" aria-label="Award badge"></div>
    </div>
  </section>
</body>
</html>
```